Creative, fresh business card design for Ripplecraft Facades

We need a fresh, creative business card design for Ripplecraft Facades. We are the manufacturer of Ripplecraft Facades in Australia. Wall panels are 2400 x 1200mm panels made from MDF and feature 3D patterns on the face of the panel. The colours to be used are green, silver/grey and white RGB
Red 187
Green 207
Blue 65.

An idea is to possibly use a watermark of one of our designs as a background (like on the "Grids" design on the left hand side of page 2 of our brochure).

Target Market(s)

Interior designers, architects, builders and home renovators

Industry/Entity Type

Business

Contact Information for Business Card

Details to go on the card are:
Our logo (attached),
Slogan: "Decorative panels for interiors and exteriors",
Contact name,
Position,
Mobile phone number,
Business address,
Business phone,
Business fax,
Website and
Email address.

I have attached a few images of our panels and our brochure for reference.

The colours of the business card should feature our logo colours which are: RGB
Red 187
Green 207
Blue 65

Requirements
Must have
• Very modern fonts and design. Some of the designs shown especially the "Prisms" design which is a popular design.
Nice to have
• Creative but simple design. Very contemporary.
Should not have
• Anything ornate or old fashioned.

```html
<!DOCTYPE html>
<html lang="en">
<head>
<meta charset="utf-8">
<title>Ripplecraft Facades – Business Card</title>
<link href="https://fonts.googleapis.com/css2?family=Questrial&display=swap" rel="stylesheet">
<style>
  :root {
    --lime: rgb(187, 207, 65);
    --card-black: #111111;
    --pattern-dark: #1a1a1a;
    --silver: #b9b9b9;
    --text-grey: #a8a8a8;
    --page: #e9e7e2;
  }
  * { box-sizing: border-box; margin: 0; padding: 0; }
  html, body {
    width: 1200px; height: 1022px; overflow: hidden;
    background: var(--page);
    font-family: "Questrial", "Century Gothic", sans-serif;
  }
  .sheet {
    width: 1200px; height: 1022px;
    display: flex; flex-direction: column; align-items: center; justify-content: center;
    gap: 36px;
  }
  .card {
    position: relative; width: 840px; height: 465px;
    background: var(--card-black); overflow: hidden;
    box-shadow: 0 10px 28px rgba(0,0,0,.28);
  }
  .card-texture {
    position: absolute; inset: 0;
    background: radial-gradient(ellipse at 35% 40%, var(--pattern-dark) 0%, var(--card-black) 75%);
  }
  /* Front: brand side */
  .brand-lockup {
    position: absolute; right: 70px; top: 120px; width: 300px;
  }
  .brand-square {
    width: 120px; height: 120px; background: var(--lime); margin-left: auto;
  }
  .brand-name {
    margin-top: 10px; background: var(--silver); color: #111;
    font-size: 27px; padding: 8px 14px; text-align: right; letter-spacing: .5px;
  }
  .brand-slogan {
    margin-top: 10px; color: var(--text-grey); font-size: 15px;
    letter-spacing: 2px; text-align: right; line-height: 1.45;
  }
  /* Back: contact side */
  .accent-band {
    position: absolute; left: 0; right: 0; bottom: 0; height: 78px; background: var(--lime);
  }
  .person { position: absolute; left: 60px; top: 58px; }
  .person-name { color: var(--lime); font-size: 36px; letter-spacing: .5px; }
  .person-role { color: var(--text-grey); font-size: 19px; margin-top: 6px; letter-spacing: 1px; }
  .contact-list {
    position: absolute; left: 60px; top: 180px; list-style: none;
    color: #d8d8d8; font-size: 21px; letter-spacing: 1px;
  }
  .contact-list li { display: flex; align-items: center; gap: 14px; height: 33px; }
  .contact-list svg { width: 18px; height: 18px; fill: var(--lime); flex: none; }
  .address {
    position: absolute; right: 70px; top: 250px; color: var(--text-grey);
    font-size: 21px; line-height: 1.5; letter-spacing: 1px; text-align: right;
  }
</style>
</head>
<body>
<main class="sheet">
  <section class="card card-front">
    <div class="card-texture" role="img" aria-label="Embossed ripple circle panel pattern"></div>
    <div class="brand-lockup">
      <div class="brand-square"></div>
      <div class="brand-name">Ripplecraft Facades</div>
      <p class="brand-slogan">decorative panels for<br>interiors &amp; landscapes</p>
    </div>
  </section>

  <section class="card card-back">
    <div class="card-texture" role="img" aria-label="Embossed ripple circle panel pattern"></div>
    <div class="accent-band"></div>
    <div class="person">
      <p class="person-name">Dana Whitfield</p>
      <p class="person-role">President</p>
    </div>
    <ul class="contact-list">
      <li><svg viewBox="0 0 18 18"><rect x="5" y="1" width="8" height="16" rx="1.5"/></svg>041. 552. 3187</li>
      <li><svg viewBox="0 0 18 18"><path d="M4 1l3 4-2 2c1 2 4 5 6 6l2-2 4 3-2 3C8 17 1 10 1 4z"/></svg>029. 604. 1175</li>
      <li><svg viewBox="0 0 18 18"><rect x="4" y="1" width="10" height="5"/><rect x="1" y="6" width="16" height="7"/><rect x="4" y="11" width="10" height="6"/></svg>029. 604. 1176</li>
      <li><svg viewBox="0 0 18 18"><path d="M1 4h16v11H1z M1 4l8 6 8-6" stroke="#111" stroke-width="1"/></svg>dana@ripplecraft.net</li>
      <li><svg viewBox="0 0 18 18"><circle cx="9" cy="9" r="8"/><path d="M1 9h16M9 1v16" stroke="#111" stroke-width="1.2"/></svg>www.ripplecraft.net</li>
    </ul>
    <p class="address">2140 Harbour Lane<br>Westmere, NSW 2150</p>
  </section>
</main>
</body>
</html>
```